Business card for law firm

Need business card for new law firm. Think confident, authoritative, conservative, but not stuffy or old-fashioned.

Contact Information for Business Card

Content for card - logo (uploaded), plus the following:

Paul Whitcombe (larger font)
Managing Partner (larger font, but not as large as name)
Level 9, 7 Ferris Lane
Sydney NSW 2000
Main Tel 02 9364 2710
Direct Tel 02 8472 3159
Email paul@qvlegal.com.au
www.qvlegal.com.au

Letterhead design should include logo plus:
Level 9, 7 Ferris Lane
Sydney NSW 2000
Tel 02 8472 3159
www.qvlegal.com.au

```html
<!DOCTYPE html>
<html lang="en">
<head>
<meta charset="UTF-8">
<title>Quayvale Lawyers – Business Card</title>
<link href="https://fonts.googleapis.com/css2?family=Roboto:wght@400;500;700&display=swap" rel="stylesheet">
<style>
  :root {
    --backdrop: #d3e6ec;
    --ink: #080808;
    --paper: #ffffff;
    --navy: #232a63;
    --navy-deep: #161b45;
    --text-dark: #111111;
    --text-light: #ffffff;
  }
  * { margin: 0; padding: 0; box-sizing: border-box; }
  html, body {
    width: 1200px; height: 900px; overflow: hidden;
    background: var(--backdrop);
    font-family: "Roboto", Arial, sans-serif;
  }
  .stage { position: relative; width: 1200px; height: 900px; }

  .card {
    position: absolute;
    width: 600px; height: 360px;
    border-radius: 22px;
    overflow: hidden;
    box-shadow: 0 6px 18px rgba(0,0,0,0.18);
  }

  /* Front */
  .card-front { left: 80px; top: 70px; background: var(--ink); color: var(--text-light); }
  .front-brand {
    position: absolute; left: 0; right: 0; top: 108px;
    display: flex; flex-direction: column; align-items: center;
  }
  .brand-mark { width: 34px; height: 34px; background: var(--text-light); margin-bottom: 22px; }
  .brand-name {
    font-weight: 400; font-size: 50px; letter-spacing: 4px; line-height: 1;
  }
  .brand-sub {
    font-weight: 400; font-size: 18px; letter-spacing: 22px; margin-top: 14px; padding-left: 22px;
  }
  .front-web {
    position: absolute; left: 0; right: 0; bottom: 34px;
    text-align: center; font-size: 15px; letter-spacing: 0.3px;
  }

  /* Back */
  .card-back { left: 520px; top: 470px; background: var(--paper); }
  .back-art { position: absolute; inset: 0; }
  .back-brand {
    position: absolute; left: 38px; top: 46px;
    display: flex; flex-direction: column; align-items: center;
    color: var(--text-dark); width: 250px;
  }
  .back-brand .brand-mark { background: var(--navy); width: 30px; height: 30px; margin-bottom: 14px; }
  .back-brand .brand-name { font-size: 34px; letter-spacing: 2px; }
  .back-brand .brand-sub { font-size: 12px; letter-spacing: 15px; margin-top: 8px; padding-left: 15px; }

  .contact-list { position: absolute; left: 38px; top: 212px; list-style: none; }
  .contact-item {
    display: flex; align-items: center; gap: 12px;
    height: 30px; font-size: 15.5px; color: var(--text-dark);
  }
  .contact-icon { width: 22px; height: 22px; flex: none; }

  .holder {
    position: absolute; left: 280px; top: 44px; width: 270px;
    text-align: center; color: var(--text-light);
  }
  .holder-name { font-weight: 700; font-size: 21px; }
  .holder-role { font-weight: 400; font-size: 12px; margin-top: 3px; }

  .address {
    position: absolute; left: 380px; top: 236px; width: 200px;
    text-align: center; color: var(--text-light); font-size: 14px; line-height: 1.4;
  }
  .address-pin { width: 14px; height: 18px; display: block; margin: 0 auto 8px; }
</style>
</head>
<body>
<main class="stage">

  <section class="card card-front" aria-label="Card front">
    <div class="front-brand">
      <span class="brand-mark"></span>
      <span class="brand-name">QUAYVALE</span>
      <span class="brand-sub">LAWYERS</span>
    </div>
    <p class="front-web">www.qvlegal.com.au</p>
  </section>

  <section class="card card-back" aria-label="Card back">
    <svg class="back-art" viewBox="0 0 600 360" aria-hidden="true">
      <defs>
        <linearGradient id="edge-shade" x1="0" y1="0" x2="1" y2="0">
          <stop offset="0" stop-color="#000" stop-opacity="0"/>
          <stop offset="1" stop-color="#000" stop-opacity="0.18"/>
        </linearGradient>
      </defs>
      <polygon points="255,0 270,0 370,360 350,360" fill="url(#edge-shade)"/>
      <polygon points="270,0 600,0 600,360 370,360" fill="var(--ink)"/>
      <polygon points="262,110 292,110 292,128" fill="var(--navy-deep)"/>
      <polygon points="262,52 585,30 585,92 262,110" fill="var(--navy)"/>
    </svg>

    <div class="back-brand">
      <span class="brand-mark"></span>
      <span class="brand-name">QUAYVALE</span>
      <span class="brand-sub">LAWYERS</span>
    </div>

    <ul class="contact-list">
      <li class="contact-item">
        <svg class="contact-icon" viewBox="0 0 22 22"><rect width="22" height="22" fill="var(--navy)"/><path d="M7 5l2.5 3-1.5 1.5c.8 1.8 2 3 3.8 3.8L13.3 12l3 2.5-1.5 2.3C10 16.5 5.5 12 5 7.2z" fill="#fff"/></svg>
        <span>02 9364 2710</span>
      </li>
      <li class="contact-item">
        <svg class="contact-icon" viewBox="0 0 22 22"><rect width="22" height="22" fill="var(--navy)"/><rect x="5" y="9" width="12" height="8" rx="1" fill="none" stroke="#fff" stroke-width="1.4"/><rect x="7" y="5" width="8" height="4" fill="none" stroke="#fff" stroke-width="1.4"/></svg>
        <span>02 8472 3159</span>
      </li>
      <li class="contact-item">
        <svg class="contact-icon" viewBox="0 0 22 22"><rect width="22" height="22" fill="var(--navy)"/><rect x="4.5" y="6.5" width="13" height="9" fill="none" stroke="#fff" stroke-width="1.4"/><path d="M4.5 6.5l6.5 5 6.5-5" fill="none" stroke="#fff" stroke-width="1.4"/></svg>
        <span>paul@qvlegal.com.au</span>
      </li>
      <li class="contact-item">
        <svg class="contact-icon" viewBox="0 0 22 22"><rect width="22" height="22" fill="var(--navy)"/><circle cx="11" cy="11" r="6" fill="none" stroke="#fff" stroke-width="1.4"/><path d="M5 11h12M11 5c-3 3.5-3 8.5 0 12M11 5c3 3.5 3 8.5 0 12" fill="none" stroke="#fff" stroke-width="1.1"/></svg>
        <span>www.qvlegal.com.au</span>
      </li>
    </ul>

    <div class="holder">
      <p class="holder-name">Paul Whitcombe</p>
      <p class="holder-role">Managing Partner</p>
    </div>

    <div class="address">
      <svg class="address-pin" viewBox="0 0 14 18"><path d="M7 0a6 6 0 0 1 6 6c0 4.5-6 12-6 12S1 10.5 1 6a6 6 0 0 1 6-6z" fill="#fff"/><circle cx="7" cy="6" r="2.2" fill="var(--ink)"/></svg>
      <p>Level 9, 7 Ferris Lane</p>
      <p>Sydney NSW 2000</p>
    </div>
  </section>

</main>
</body>
</html>
```